Redesign two existing website pages and one new landing page for dental office

I need to redesign two webpages on my dental website, the Home page (http://velbridgedental.com) and the Dental Implant Services page (http://www.velbridgedental.com/dental-implant-services) and also create a landing page for the Dental Implant Services page.

Please use the same color scheme, slogans and subtitles for the redesign pages and create a reserved video spot on each page. The video spots should not be too big but not too small either and positioned in a central key location on each of the pages. The final redesigned pages should communicate leadership, confidence and trust.

The new landing page for the Dental implant Services page must not have any hyperlinks on the page and must entice the viewer to give name and email before downloading a "Free" eBook called "Is a Fuller Smile Worth the Wait?" Any added photo images to this new page must be smiling.
Updates

Project Deadline Extended Reason: I got feedback that my project was not long enough so I'm extending it by 5 days. Added Thursday, April 16, 2015

Target Market(s)

People who are middle-age to seniors.

Industry/Entity Type

Dental

Coding

Coded - Design and coding required

Number of Pages Required

3 page

Requirements
Must have
• Compatible with existing website colors and theme.

```html
<!DOCTYPE html>
<html lang="en">
<head>
<meta charset="utf-8">
<title>Velbridge Dental Care – Home</title>
<link href="https://fonts.googleapis.com/css2?family=Open+Sans:wght@300;400;600;700&display=swap" rel="stylesheet">
<style>
:root{
  --ink:#2b2b2b;
  --muted:#7a7a7a;
  --teal:#2f5a4f;
  --teal-dark:#24463d;
  --teal-soft:#6f9e91;
  --bar:#222222;
  --footer:#333333;
  --footer-deep:#2a2a2a;
  --band:#d4dedc;
  --hero:#dfe6e6;
  --white:#ffffff;
}
*{box-sizing:border-box;margin:0;padding:0}
html,body{width:712px;height:1200px;overflow:hidden;background:var(--white)}
body{font-family:"Open Sans",Arial,sans-serif;color:var(--ink);position:relative}
.abs{position:absolute}
a{color:inherit;text-decoration:none}

/* top bar */
.topbar{left:0;top:0;width:712px;height:21px;background:var(--bar);color:#aaa;font-size:7.5px}
.topbar .welcome{left:66px;top:6px}
.topbar .links{right:66px;top:6px;display:flex;gap:18px}
.topbar .links span{display:flex;align-items:center;gap:5px}

/* header */
.header{left:0;top:21px;width:712px;height:80px;background:var(--white)}
.brand{left:66px;top:28px;display:flex;align-items:center;gap:8px;font-size:24px;font-weight:400;color:var(--teal-soft)}
.brand .dot{width:10px;height:10px;border-radius:50%;background:var(--teal-soft)}
.callout{right:64px;top:10px;text-align:right;font-size:8px;color:#333;line-height:1.5}
.callout .phone{font-size:12px;color:var(--teal-soft);font-weight:400;line-height:1.4}
.social{display:flex;gap:3px;justify-content:flex-end;margin-top:3px}
.social i{width:14px;height:14px;border-radius:50%;display:block}

/* nav */
.nav{left:0;top:101px;width:712px;height:32px;background:linear-gradient(#3f7064,#2a5147);border-top:1px solid #4d7f72}
.nav ul{list-style:none;display:flex;position:absolute;left:66px;top:0}
.nav li{width:97px;height:31px;line-height:31px;text-align:center;color:#fff;font-size:8.5px;font-weight:600;border-right:1px solid #24463d;box-shadow:1px 0 0 #4c7d71}
.nav li.active{background:rgba(0,0,0,.12)}

/* hero */
.hero{left:0;top:133px;width:712px;height:278px;background:radial-gradient(ellipse at 60% 50%,#eef2f1,#cfd9d9);border-bottom:3px solid #3a3a3a}
.hero h1{left:66px;top:86px;font-size:21px;font-weight:400;line-height:1.3;color:#333;letter-spacing:-.3px;white-space:nowrap;z-index:2}
.hero h1 strong{font-weight:600;color:var(--teal)}
.hero .cta{left:66px;top:155px;width:150px;height:30px;background:#1f1f1f;color:#fff;font-size:9.5px;font-weight:600;line-height:30px;text-align:center;border-radius:2px}
.hero .photo{left:384px;top:3px;width:292px;height:272px;border-radius:40px 40px 0 0;background:linear-gradient(160deg,#e8d2bf,#c9a889 55%,#9bb888);z-index:1}
.dots{left:70px;top:252px;display:flex;gap:3px}
.dots i{width:5px;height:5px;border-radius:50%;background:#a9b2b1;display:block}
.dots i:first-child{background:#333}

/* feature band */
.features{left:0;top:414px;width:712px;height:227px;background:var(--band)}
.feature{top:0;width:174px;height:227px}
.feature h2{position:absolute;top:22px;font-size:11.5px;font-weight:600;color:#2b2b2b;white-space:nowrap}
.feature .thumb{position:absolute;top:48px;width:174px;height:84px;border:3px solid #fff;box-shadow:0 1px 2px rgba(0,0,0,.15)}
.feature h3{position:absolute;top:142px;font-size:9.5px;font-weight:400;color:#333;white-space:nowrap}
.feature p{position:absolute;top:158px;font-size:7.3px;line-height:1.6;color:var(--muted);width:178px}
.feature .more{position:absolute;top:200px;font-size:7.5px;font-weight:600;color:#222}
.divider{top:14px;width:1px;height:200px;background:#c3cfcd}

/* services */
.services{left:0;top:641px;width:712px;height:292px;background:linear-gradient(#fff 40%,#e3ecea)}
.services h2{left:0;width:712px;top:30px;text-align:center;font-size:23px;font-weight:300;color:var(--teal-soft)}
.services h2 strong{font-weight:600;color:var(--teal)}
.services .intro{left:146px;width:420px;top:66px;text-align:center;font-size:8px;line-height:1.65;color:var(--muted)}
.service{top:128px;width:150px;text-align:center}
.service svg{display:block;margin:0 auto}
.service h3{margin-top:18px;font-size:10px;font-weight:600;color:#2b2b2b;white-space:nowrap}
.service ul{list-style:none;margin-top:8px;font-size:8px;line-height:1.65;color:var(--muted)}

/* news */
.news{left:0;top:933px;width:712px;height:33px;background:var(--bar);color:#ddd;font-size:7.5px}
.news .label{left:70px;top:11px;font-weight:600;font-size:8.5px;color:#fff}
.news .text{left:134px;top:12px}
.news .arrows{right:83px;top:7px;display:flex;gap:3px}
.news .arrows span{width:15px;height:15px;border:1px solid #777;border-radius:50%;display:flex;align-items:center;justify-content:center}

/* footer */
.footer{left:0;top:966px;width:712px;height:198px;background:var(--footer);color:#9a9a9a}
.footer h4{position:absolute;top:16px;font-size:11.5px;font-weight:400;color:#fff}
.footer .col{position:absolute;top:0;width:180px;height:198px}
.footer .portrait{position:absolute;top:42px;left:0;width:60px;height:53px;background:linear-gradient(135deg,#d9c2ad,#a88a70)}
.footer .side{position:absolute;top:42px;left:66px;width:110px;font-size:7.3px;line-height:1.65}
.footer .under{position:absolute;top:96px;left:0;width:178px;font-size:7.3px;line-height:1.65}
.post{position:absolute;left:0;width:180px;height:35px}
.post .date{position:absolute;left:0;top:0;width:36px;height:35px;background:var(--footer-deep);text-align:center;color:#bbb}
.post .date b{display:block;font-size:13px;font-weight:400;line-height:16px;margin-top:4px}
.post .date small{display:block;font-size:7px;line-height:10px}
.post p{position:absolute;left:43px;top:5px;width:130px;font-size:7px;line-height:1.6}
.footer .map{position:absolute;top:41px;left:0;width:172px;height:71px;background:linear-gradient(135deg,#e8e4da,#d7dccf 60%,#c9d6e0)}
.footer dl{position:absolute;top:124px;left:0;width:180px;font-size:7.3px;line-height:1.65;display:grid;grid-template-columns:38px 1fr}
.copyright{left:0;top:1164px;width:712px;height:36px;background:var(--footer);border-top:1px solid #3d3d3d;color:#888;font-size:7.5px;text-align:center;line-height:34px}
</style>
</head>
<body>

<div class="abs topbar">
  <span class="abs welcome">Welcome To Velbridge Dental Care...!</span>
  <div class="abs links">
    <span><svg width="6" height="9" viewBox="0 0 6 9"><rect x=".5" y=".5" width="5" height="8" rx="1" fill="none" stroke="#aaa"/></svg>Get Dr.Velbridge Mobile App</span>
    <span><svg width="7" height="9" viewBox="0 0 7 9"><rect x=".5" y=".5" width="6" height="8" fill="none" stroke="#aaa"/><path d="M2 3h3M2 5h3M2 7h2" stroke="#aaa"/></svg>Patient online Forms</span>
  </div>
</div>

<header class="abs header">
  <div class="abs brand"><span class="dot"></span>Velbridge Dental Care</div>
  <div class="abs callout">
    <div>Call Us Today!</div>
    <div class="phone">(555) 218 4760</div>
    <div>Harlow Creek, TX 77990, United States</div>
    <div class="social"><i style="background:#3b5998"></i><i style="background:#2fa7e0"></i><i style="background:#d9452f"></i><i style="background:#1a8ac0"></i></div>
  </div>
</header>

<nav class="abs nav">
  <ul>
    <li class="active">HOME</li><li>ABOUT US</li><li>DENTAL SERVICES</li><li>OUR BLOG</li><li>CONTACT US</li><li>TESTIMONIALS</li>
  </ul>
</nav>

<section class="abs hero">
  <h1 class="abs">Life-Changing Family<br><strong>Dental Care In Harlow Creek</strong></h1>
  <a class="abs cta">REQUEST AN APPOINTMENT</a>
  <div class="abs photo" role="img" aria-label="Photo of a smiling multi-generation family"></div>
  <div class="abs dots"><i></i><i></i><i></i><i></i></div>
</section>

<section class="abs features">
  <div class="abs feature" style="left:66px">
    <h2>DENTAL HYGIENE SERVICES</h2>
    <div class="thumb" role="img" aria-label="Photo of a family brushing their teeth" style="background:linear-gradient(135deg,#e9dccf,#c8a88c)"></div>
    <h3>Achieve Better Health With Prevention</h3>
    <p>Lorem ipsum dolor sit amet, consectetur adipiscing elit, sed do eiusmod tempor incididunt ut labore et dolore magna aliqua...</p>
    <a class="more">Read More »</a>
  </div>
  <div class="abs divider" style="left:254px"></div>
  <div class="abs feature" style="left:270px">
    <h2>DENTAL EMERGENCY SERVICES</h2>
    <div class="thumb" role="img" aria-label="Photo of a woman with tooth pain" style="background:linear-gradient(135deg,#f1e6dd,#c98e62)"></div>
    <h3>Stop Pain From Tooth Trauma &amp; Infection</h3>
    <p>Lorem ipsum dolor sit amet, consectetur adipiscing elit, sed do eiusmod tempor incididunt ut labore et dolore magna aliqua...</p>
    <a class="more">Read More »</a>
  </div>
  <div class="abs divider" style="left:458px"></div>
  <div class="abs feature" style="left:474px">
    <h2 style="top:26px">OUR VIDEO</h2>
    <div class="thumb" role="img" aria-label="Video still of a dentist with a patient" style="background:linear-gradient(135deg,#b7c6cf,#d9c3ae)">
      <svg class="abs" style="left:63px;top:18px" width="40" height="40" viewBox="0 0 40 40"><circle cx="20" cy="20" r="19" fill="rgba(40,40,40,.6)"/><path d="M16 12l12 8-12 8z" fill="#fff"/></svg>
    </div>
    <h3>Lorem ipsum dolor sit amet consectetur</h3>
    <p>Lorem ipsum dolor sit amet, consectetur adipiscing elit, sed do eiusmod tempor incididunt ut labore et dolore magna aliqua...</p>
    <a class="more">Read More »</a>
  </div>
</section>

<section class="abs services">
  <h2 class="abs">OUR <strong>SERVICES</strong></h2>
  <p class="abs intro">Lorem ipsum dolor sit amet, consectetur adipiscing elit, sed do eiusmod tempor incididunt ut labore et dolore magna aliqua. Ut enim ad minim veniam, quis nostrud exercitation ullamco laboris nisi ut aliquip ex ea commodo consequat.</p>

  <div class="abs service" style="left:56px">
    <svg width="56" height="56" viewBox="0 0 56 56"><circle cx="28" cy="28" r="28" fill="var(--teal)"/><path d="M20 16c4-2 6 1 8 1s4-3 8-1c4 2 3 9 1 13-1 3-1 11-4 11-2 0-2-8-5-8s-3 8-5 8c-3 0-3-8-4-11-2-4-3-11 1-13z" fill="#fff"/></svg>
    <h3>BEAUTIFUL DENTURES</h3>
    <ul><li>What is a Denture?</li><li>Who Needs a Denture?</li><li>Just How Are Dentures Made?</li></ul>
  </div>
  <div class="abs service" style="left:207px">
    <svg width="56" height="56" viewBox="0 0 56 56"><circle cx="28" cy="28" r="28" fill="var(--teal)"/><path d="M13 27c5-4 9-5 15-2 6-3 10-2 15 2-4 6-9 9-15 9s-11-3-15-9z" fill="#fff"/><path d="M15 27c6 2 20 2 26 0" stroke="var(--teal)" stroke-width="1.5" fill="none"/></svg>
    <h3>COSMETIC DENTISTRY</h3>
    <ul><li>Whiten Your Teeth</li><li>Porcelain Veneers</li><li>Clear Aligner Therapy Orthodontics</li></ul>
  </div>
  <div class="abs service" style="left:357px">
    <svg width="56" height="56" viewBox="0 0 56 56"><circle cx="28" cy="28" r="28" fill="var(--teal)"/><path d="M20 14c3-2 5 0 8 0s5-2 8 0c2 2 1 7 0 9H20c-1-2-2-7 0-9z" fill="#fff"/><path d="M22 25h12M23 29h10M24 33h8M25 37h6M26 41h4" stroke="#fff" stroke-width="2"/></svg>
    <h3>DENTAL IMPLANT SERVICES</h3>
    <ul><li>Anchorage to the jaw bone</li><li>Replaces 1 or more missing teeth</li><li>Stabilizes loose, floppy dentures</li></ul>
  </div>
  <div class="abs service" style="left:507px">
    <svg width="56" height="56" viewBox="0 0 56 56"><circle cx="28" cy="28" r="28" fill="var(--teal)"/><path d="M17 16l3 10v14" stroke="#fff" stroke-width="3" fill="none" stroke-linecap="round"/><circle cx="35" cy="19" r="6" fill="none" stroke="#fff" stroke-width="2.5"/><path d="M35 25v15" stroke="#fff" stroke-width="3" stroke-linecap="round"/></svg>
    <h3>SEDATION DENTISTRY</h3>
    <ul><li>Control Dental Fear with Sedation Dentistry</li><li>Dental Pain Management</li><li>Relaxed and Tranquil Treatment</li></ul>
  </div>
</section>

<div class="abs news">
  <span class="abs label">LATEST NEWS:</span>
  <span class="abs text">Lorem ipsum dolor sit amet, consectetur adipisicing elit, sed do eiusmod tempor incididunt ut labore et dolore magna aliqua.</span>
  <div class="abs arrows">
    <span><svg width="6" height="7" viewBox="0 0 6 7"><path d="M4 1L1.5 3.5 4 6" stroke="#aaa" fill="none"/></svg></span>
    <span><svg width="6" height="7" viewBox="0 0 6 7"><path d="M2 1l2.5 2.5L2 6" stroke="#aaa" fill="none"/></svg></span>
  </div>
</div>

<footer class="abs footer">
  <div class="col" style="left:66px">
    <h4>Don’t Wait ‘til it Hurts!</h4>
    <div class="portrait" role="img" aria-label="Photo of a woman holding her jaw in pain"></div>
    <p class="side">Lorem ipsum dolor sit amet, consectetur adipiscing elit, sed do eiusmod tempor incididunt ut labore et dolore magna aliqua...</p>
    <p class="under">Lorem ipsum dolor sit amet, consectetur adipiscing elit, sed do eiusmod tempor incididunt ut labore et dolore magna aliqua...</p>
  </div>
  <div class="col" style="left:270px">
    <h4>Recent Blog Posts</h4>
    <div class="post" style="top:41px"><div class="date"><b>15</b><small>April</small></div><p>Conscious Sedation: A Way to Deal with Anxiety at the Dentist’s Office</p></div>
    <div class="post" style="top:83px"><div class="date"><b>15</b><small>April</small></div><p>Pediatric Dentists and Their Importance in Today’s World</p></div>
    <div class="post" style="top:124px"><div class="date"><b>15</b><small>April</small></div><p>Conscious Sedation: A Way to Deal with Anxiety at the Dentist’s Office</p></div>
  </div>
  <div class="col" style="left:475px">
    <h4>Contact Us</h4>
    <div class="map" role="img" aria-label="Map showing the office location"></div>
    <dl>
      <dt>Address:</dt><dd>4820 Meadow Parkway, Ste. #220, Harlow Creek, TX 77990</dd>
      <dt>Email:</dt><dd>info@velbridgedental.com</dd>
      <dt>Phone:</dt><dd>(555) 218 4760</dd>
      <dt>Fax:</dt><dd>(555) 218 4760</dd>
    </dl>
  </div>
</footer>

<div class="abs copyright">Copyrights © 2015 Velbridge Dental Care, Larkstone Medical Center.com - All Rights reserved</div>

</body>
</html>
```